Where's my Gym Buddy? looking to do two promotions as listed in project description

looking for two designs.

1: selfie frame design!! (wording) Icebound Hustle Gala, my Summer fitness has started, Tag a friend who should be joining me. T.C Tag your posts to @kestrelhubsydney to win points for the competition. (Snow graphic) in a selfie frame design. this needs to be the same design but across different departments as seen at the top of the photo's I've attached EG: #kestrelhubfitness #kestrelhubindoor #kestrelhubswim #kestrelhubwyong

2: Selfie Frame Design!! (Wording) Where's my gym buddy?, Tag a friend who should be at the gym, T.C.Tag your posts to @kestrelhubsydney to win points for the competition. Mister Plumtree Feel Selfie frame design

Target Market(s)

Gym Members

Industry/Entity Type

Gym

Colors

Designer to choose colors to be used in the design.

Requirements
Must have
• quirky and funky design, must include wording listed, must be a selfie frame design
Should not have
• whilst we are a big corporate gym, we pride ourselves on having really funky advertisements, so please no boring business corporate typical designs

```html
<!DOCTYPE html>
<html lang="en">
<head>
<meta charset="utf-8">
<title>Where's My Gym Buddy? – Selfie Frame</title>
<link rel="stylesheet" href="https://fonts.googleapis.com/css2?family=Fredoka:wght@500;600;700&display=swap">
<style>
  :root {
    --band: #f26a21;
    --accent: #1d5c8c;
    --ink: #141414;
    --paper: #ffffff;
    --shadow: rgba(0, 0, 0, 0.25);
  }
  * { box-sizing: border-box; margin: 0; padding: 0; }
  html, body {
    width: 848px;
    height: 1200px;
    overflow: hidden;
    background: var(--paper);
  }
  .poster {
    position: relative;
    width: 848px;
    height: 1200px;
    background: var(--paper);
    font-family: "Fredoka", "Trebuchet MS", sans-serif;
    overflow: hidden;
  }

  /* Brand block */
  .brand {
    position: absolute;
    top: 100px;
    right: 91px;
    display: flex;
    flex-direction: column;
    align-items: flex-end;
    color: var(--ink);
    font-weight: 600;
  }
  .brand-row {
    display: flex;
    align-items: center;
    gap: 14px;
  }
  .brand-square {
    width: 40px;
    height: 40px;
    background: var(--ink);
  }
  .brand-name {
    font-size: 64px;
    line-height: 1;
  }
  .brand-tagline {
    margin-top: 10px;
    font-size: 33px;
    line-height: 1;
  }

  /* Banded backdrop */
  .bands {
    position: absolute;
    left: 0;
    right: 0;
    top: 277px;
    bottom: 0;
    background: repeating-linear-gradient(
      to bottom,
      var(--band) 0 30px,
      var(--paper) 30px 70px
    );
  }

  /* Headline banner */
  .headline {
    position: absolute;
    left: 56px;
    top: 248px;
    width: 738px;
    height: 140px;
    background: var(--paper);
    border: 6px solid var(--accent);
    border-radius: 18px;
    transform: rotate(-1.4deg);
    box-shadow: 3px 4px 6px var(--shadow);
    display: flex;
    align-items: center;
    justify-content: center;
    gap: 16px;
  }
  .headline-wheres {
    color: var(--accent);
    font-size: 86px;
    font-weight: 700;
    line-height: 1;
  }
  .headline-buddy {
    display: flex;
    flex-direction: column;
    align-items: center;
    color: var(--band);
    font-weight: 700;
    line-height: 0.9;
  }
  .headline-buddy .small { font-size: 38px; }
  .headline-buddy .large { font-size: 58px; }
  .headline-mark {
    color: var(--accent);
    font-size: 80px;
    font-weight: 700;
    line-height: 1;
  }

  /* Selfie window */
  .selfie-frame {
    position: absolute;
    left: 138px;
    top: 411px;
    width: 573px;
    height: 590px;
    background: var(--paper);
  }
  .selfie-window {
    position: absolute;
    left: 8px;
    top: 3px;
    right: 10px;
    bottom: 14px;
    background: var(--paper);
    box-shadow: inset 0 0 9px var(--shadow);
  }

  /* Captions */
  .caption-tag {
    position: absolute;
    left: 39px;
    top: 1016px;
    width: 766px;
    height: 56px;
    background: var(--paper);
    border: 5px solid var(--accent);
    border-radius: 10px;
    transform: rotate(-1deg);
    box-shadow: 3px 3px 5px var(--shadow);
    display: flex;
    align-items: center;
    padding-left: 18px;
    color: var(--band);
    font-size: 31px;
    font-weight: 700;
    line-height: 1;
  }
  .caption-terms {
    position: absolute;
    left: 21px;
    top: 1088px;
    width: 803px;
    height: 98px;
    background: var(--paper);
    border: 6px solid var(--band);
    border-radius: 10px;
    transform: rotate(-0.6deg);
    box-shadow: 3px 3px 5px var(--shadow);
    padding: 10px 40px 0 36px;
  }
  .caption-terms .entry {
    color: var(--accent);
    font-size: 27px;
    font-weight: 700;
    line-height: 1.0;
  }
  .caption-terms .conditions {
    margin-top: 2px;
    text-align: right;
    color: var(--band);
    font-size: 21px;
    font-weight: 600;
    line-height: 1;
  }
</style>
</head>
<body>
  <main class="poster">
    <div class="bands" aria-hidden="true"></div>

    <header class="brand">
      <div class="brand-row">
        <span class="brand-square" aria-hidden="true"></span>
        <span class="brand-name">kestrel hub</span>
      </div>
      <span class="brand-tagline">fitness &amp; wellbeing centre</span>
    </header>

    <h1 class="headline">
      <span class="headline-wheres">Where's</span>
      <span class="headline-buddy">
        <span class="small">MY GYM</span>
        <span class="large">BUDDY</span>
      </span>
      <span class="headline-mark">?</span>
    </h1>

    <section class="selfie-frame" aria-label="Selfie window">
      <div class="selfie-window"></div>
    </section>

    <p class="caption-tag">Tag a friend who should be at the gym,</p>

    <div class="caption-terms">
      <p class="entry">Tag your posts to @kestrelhubcrew to win<br>points for the competition.</p>
      <p class="conditions">Terms + Conditions At Reception</p>
    </div>
  </main>
</body>
</html>
```